Design a compelling Tarnwove Business Card that will drive people to my site

I want a business card that I can give to people—less to tell them who I am and more to direct them to my website. My website is a portal for Pelmor Aquatics Officials and a place for people who want to become Pelmor Aquatics Officials.
I am uploading my official company logo as well as a business card mockup that I did on my own. Please feel free to completely stray from this design.
I've included a screen recording of the homepage of my website as well.
Target Market(s)
Pelmor Aquatics Officials and people who desire to become one
Contact Information for Business Card
website url
Look and feel
Each slider illustrates characteristics of the customer's brand and the style your logo design should communicate.

```html
<!DOCTYPE html>
<html lang="en">
<head>
<meta charset="utf-8">
<title>Tarnwove Business Card</title>
<link rel="stylesheet" href="https://fonts.googleapis.com/css2?family=Montserrat:wght@400;500;700&display=swap">
<style>
  :root {
    --page-bg: #e9ebf0;
    --brand-blue: #3a55a8;
    --brand-light: #93a8d9;
    --card-white: #ffffff;
    --text-white: #ffffff;
    --icon-ring: rgba(255, 255, 255, 0.55);
  }
  * { box-sizing: border-box; margin: 0; padding: 0; }
  html, body {
    width: 1200px;
    height: 912px;
    overflow: hidden;
    background: var(--page-bg);
    font-family: "Montserrat", sans-serif;
  }
  .canvas {
    position: relative;
    width: 1200px;
    height: 912px;
  }
  .card {
    position: absolute;
    width: 640px;
    height: 366px;
    border-radius: 20px;
    overflow: hidden;
    background: var(--brand-blue);
    box-shadow: 0 10px 28px rgba(20, 30, 60, 0.22);
  }
  .card--front { left: 80px; top: 60px; }
  .card--back { left: 480px; top: 486px; }

  /* Front */
  .front-brand {
    position: absolute;
    left: 0; right: 0;
    top: 128px;
    text-align: center;
    color: var(--text-white);
    font-weight: 700;
    font-size: 72px;
    letter-spacing: -2px;
    line-height: 1;
  }
  .front-tagline {
    position: absolute;
    left: 0; right: 0;
    top: 268px;
    text-align: center;
    color: var(--text-white);
    font-weight: 400;
    font-size: 17px;
    letter-spacing: 0.5px;
  }

  /* Back */
  .back-shape {
    position: absolute;
    inset: 0;
  }
  .back-brand {
    position: absolute;
    left: 330px;
    top: 132px;
    width: 300px;
    text-align: center;
    color: var(--brand-blue);
    font-weight: 700;
    font-size: 46px;
    letter-spacing: -1.5px;
    line-height: 1;
  }
  .contact {
    position: absolute;
    left: 48px;
    top: 150px;
    color: var(--text-white);
  }
  .contact__name {
    color: var(--brand-light);
    font-weight: 700;
    font-size: 27px;
    line-height: 1.1;
  }
  .contact__title {
    font-weight: 400;
    font-size: 19px;
    margin-top: 4px;
  }
  .contact__rule {
    width: 34px;
    height: 1px;
    background: var(--brand-light);
    margin: 14px 0 12px;
  }
  .contact__list { list-style: none; }
  .contact__item {
    display: flex;
    align-items: center;
    gap: 12px;
    font-size: 19px;
    font-weight: 400;
    height: 34px;
  }
  .contact__icon {
    width: 24px;
    height: 24px;
    flex: none;
  }
</style>
</head>
<body>
<main class="canvas">

  <section class="card card--front" role="img" aria-label="Tarnwove card front: blue field for a faint repeated brand pattern, company name and tagline">
    <div class="front-brand">Tarnwove</div>
    <p class="front-tagline">Your Lane to Poolside Officiating</p>
  </section>

  <section class="card card--back">
    <svg class="back-shape" viewBox="0 0 640 366" aria-hidden="true">
      <circle cx="520" cy="148" r="232" fill="var(--brand-light)"/>
      <circle cx="532" cy="142" r="222" fill="var(--card-white)"/>
    </svg>

    <div class="back-brand">Tarnwove</div>

    <div class="contact">
      <h1 class="contact__name">Marcus Ellery</h1>
      <p class="contact__title">CEO &amp; Founder</p>
      <div class="contact__rule"></div>
      <ul class="contact__list">
        <li class="contact__item">
          <svg class="contact__icon" viewBox="0 0 24 24" aria-hidden="true">
            <circle cx="12" cy="12" r="11" fill="none" stroke="var(--icon-ring)" stroke-width="1.2"/>
            <path d="M8.5 7.5l2 2-1.2 1.4a6 6 0 0 0 3.8 3.8l1.4-1.2 2 2-1.3 1.3c-3.5-.3-7.7-4.5-8-8z" fill="var(--text-white)"/>
          </svg>
          <span>(555) 214-7730</span>
        </li>
        <li class="contact__item">
          <svg class="contact__icon" viewBox="0 0 24 24" aria-hidden="true">
            <circle cx="12" cy="12" r="11" fill="none" stroke="var(--icon-ring)" stroke-width="1.2"/>
            <rect x="6.5" y="8" width="11" height="8" rx="1" fill="var(--text-white)"/>
            <path d="M6.8 8.4l5.2 4 5.2-4" fill="none" stroke="var(--brand-blue)" stroke-width="1"/>
          </svg>
          <span>marcus@tarnwove.com</span>
        </li>
        <li class="contact__item">
          <svg class="contact__icon" viewBox="0 0 24 24" aria-hidden="true">
            <circle cx="12" cy="12" r="11" fill="none" stroke="var(--icon-ring)" stroke-width="1.2"/>
            <g fill="none" stroke="var(--text-white)" stroke-width="1">
              <circle cx="12" cy="12" r="5.5"/>
              <ellipse cx="12" cy="12" rx="2.4" ry="5.5"/>
              <path d="M6.5 12h11M7.3 9.2h9.4M7.3 14.8h9.4"/>
            </g>
          </svg>
          <span>www.tarnwove.com</span>
        </li>
      </ul>
    </div>
  </section>

</main>
</body>
</html>
```